Automotive component supplier needs a business card design

We need a business card design for our company called Velran Global Components Ltd based in the UK. We are a supplier of interior and exterior components to premium car manufacturers such as Corvel Ashby, Hadley Fenn, Marquist and Tavarelli. We would like to see a modern business card design that uses the colour blue.

Target Market(s)

Premium automotive car manufacturers.

Industry/Entity Type

Automotive

Contact Information for Business Card

Company Name : Velran Global Components Limited
Address: 17 Marlow Yard, Upper Heath, Warwick, CV31 8QL, United Kingdom
Web Address : www.velrancomponents-example.co.uk

Font styles to use
Other font styles liked:
• Helvetica

Colors
3176b5
0255a3
85acd3
cfdeed
cee9f5
85cae6
34a6d7
0692cd
9bcb3c

Requirements
Must have
• Clear company logo and a mixture of blue colours.
Nice to have
• A high quality modern image.
Should not have
• Multiple colours.

```html
<!DOCTYPE html>
<html lang="en">
<head>
<meta charset="utf-8">
<title>Velran Global Components – Business Card</title>
<link rel="stylesheet" href="https://fonts.googleapis.com/css2?family=Lato:wght@400;700&display=swap">
<style>
  :root {
    --blue: #0a8bd0;
    --blue-deep: #0255a3;
    --green: #9bcb3c;
    --white: #ffffff;
    --ink: #1f2a33;
    --stage: #e9edf1;
  }
  * { box-sizing: border-box; margin: 0; padding: 0; }
  html, body { width: 1200px; height: 800px; overflow: hidden; }
  body {
    background: var(--stage);
    font-family: "Lato", Helvetica, Arial, sans-serif;
    display: flex;
    align-items: center;
    justify-content: center;
    gap: 40px;
  }
  .card {
    position: relative;
    width: 540px;
    height: 330px;
    border-radius: 4px;
    overflow: hidden;
    box-shadow: 0 6px 18px rgba(0, 0, 0, 0.15);
  }

  /* Back side */
  .card-back {
    background: var(--blue);
    color: var(--white);
  }
  .card-back .brand {
    position: absolute;
    top: 118px;
    left: 0;
    right: 0;
    display: flex;
    align-items: center;
    justify-content: center;
    gap: 12px;
  }
  .brand-mark {
    width: 14px;
    height: 14px;
    background: var(--green);
    flex: none;
  }
  .card-back .brand-name {
    font-weight: 700;
    font-size: 34px;
    letter-spacing: 1px;
    color: var(--white);
  }
  .card-back .web {
    position: absolute;
    bottom: 34px;
    left: 0;
    right: 0;
    text-align: center;
    font-size: 14px;
    letter-spacing: 1.5px;
  }

  /* Front side */
  .card-front { background: var(--white); }
  .card-front .wave {
    position: absolute;
    inset: 0;
    width: 100%;
    height: 100%;
  }
  .card-front .brand {
    position: absolute;
    top: 40px;
    left: 34px;
    display: flex;
    align-items: center;
    gap: 10px;
  }
  .card-front .brand-name {
    font-weight: 700;
    font-size: 24px;
    letter-spacing: 0.5px;
    color: var(--blue);
  }
  .person {
    position: absolute;
    top: 150px;
    left: 40px;
  }
  .person-name {
    font-weight: 700;
    font-size: 22px;
    color: var(--blue);
  }
  .person-role {
    font-size: 15px;
    color: var(--ink);
    margin-top: 2px;
  }
  .contact {
    position: absolute;
    top: 168px;
    left: 308px;
    color: var(--white);
    font-size: 11.5px;
    line-height: 1.35;
  }
  .contact address { font-style: normal; margin-bottom: 8px; }
  .contact ul { list-style: none; }
  .contact li {
    display: flex;
    align-items: center;
    gap: 7px;
    margin-bottom: 2px;
    white-space: nowrap;
  }
  .contact svg { width: 10px; height: 10px; fill: var(--green); flex: none; }
</style>
</head>
<body>

  <section class="card card-back" aria-label="Business card back">
    <div class="brand">
      <span class="brand-mark"></span>
      <span class="brand-name">Velran Global Components</span>
    </div>
    <p class="web">www.velrancomponents-example.co.uk</p>
  </section>

  <section class="card card-front" aria-label="Business card front">
    <svg class="wave" viewBox="0 0 540 330" preserveAspectRatio="none" aria-hidden="true">
      <path fill="var(--green)" d="M0,232 C120,222 190,172 250,117 C320,55 430,40 540,36 L540,50 C430,54 330,78 266,132 C200,188 120,238 0,250 Z"/>
      <path fill="var(--blue)" d="M0,262 C130,252 205,205 265,150 C330,90 430,68 540,62 L540,70 C440,76 345,100 280,155 C215,212 130,262 0,272 Z"/>
      <path fill="var(--blue)" d="M0,282 C140,272 220,222 280,168 C345,110 440,86 540,80 L540,330 L0,330 Z"/>
    </svg>

    <div class="brand">
      <span class="brand-mark"></span>
      <span class="brand-name">Velran Global Components</span>
    </div>

    <div class="person">
      <p class="person-name">Marten Olsby</p>
      <p class="person-role">Manager</p>
    </div>

    <div class="contact">
      <address>
        17 Marlow Yard, Upper Heath<br>
        Warwick, CV31 8QL<br>
        United Kingdom
      </address>
      <ul>
        <li>
          <svg viewBox="0 0 12 12"><path d="M2.5,0.5 L4.5,0.5 L5.3,3 L4,4.2 C4.7,5.7 6.3,7.3 7.8,8 L9,6.7 L11.5,7.5 L11.5,9.5 C11.5,10.6 10.6,11.5 9.5,11.5 C4.5,11.2 0.8,7.5 0.5,2.5 C0.5,1.4 1.4,0.5 2.5,0.5 Z"/></svg>
          512 004 2190
        </li>
        <li>
          <svg viewBox="0 0 12 12"><path d="M3,0 H9 A1,1 0 0 1 10,1 V11 A1,1 0 0 1 9,12 H3 A1,1 0 0 1 2,11 V1 A1,1 0 0 1 3,0 Z M3.5,1.5 V9 H8.5 V1.5 Z"/></svg>
          512 004 2191
        </li>
        <li>
          <svg viewBox="0 0 12 12"><path d="M0,2 H12 V10 H0 Z M1,3 L6,6.8 L11,3 V2.8 H1 Z"/></svg>
          info@velrancomponents-example.co.uk
        </li>
        <li>
          <svg viewBox="0 0 12 12"><circle cx="6" cy="6" r="5.5"/></svg>
          www.velrancomponents-example.co.uk
        </li>
      </ul>
    </div>
  </section>

</body>
</html>
```